New Wordpress Design Project - Australian native plant nursery

I'm Seeking a wordpress website with landing page with contact details and social links, that page will link to another 4 pages. I'm happy to just add in the information once the template is set up (draft text provided on word doc).
Needing pages of information pages for:
- Nursery, what we carry and that we provide garden design services, pictures of plants and gardens
- Native flowers & what we provide, flower arrangements for weddings, special occasions, pictures
- Giftwear short blurb that we carry local artisan giftwear, pictures
- about us with history of the nursery & pictures
* Also wanting a link for e-gift cards. The link will go to an external page (square) so I don’t need to set up the website for purchases.
Social media links
Social links
https://www.facebook.com/ThePebbleHollowGarden
https://www.instagram.com/thepebblehollowgardennursery

Two local native nursery websites that I like the style of:
https://www.brimbarkstemnursery.com.au/
https://www.telvoni.com.au/

I'm using two versions of our logo, we have the smaller circle and then the other logo which is stretched out. We have used the second design for our signs at the nursery, I've asked the sign guy for a copy of the design as I don't currently have one. I have vector files of the other design.

We have wordpress set up with elemantor and hosting with godaddy, I can send you the logon details once design is confirmed.

Target Market(s)

Anyone who likes gardening, we have a pretty even spread of customers across male/female and all ages

Industry/Entity Type

Garden centre with native plants, flowers and giftwear

Coding

Coded - Design and coding required

Colors
0054AA
0677BA
7BADD7
CADEEF
E8F1F8
0094D4
00A9DD
6FCCEA
C7EBF8
E9F6FB
00AB8E
00BBA5
67D7C9
C6EFE9
E9F9F6

Requirements
Must have
• Organic/modern/minimalist design
Nice to have
• Blue/white/green, flannel flowers as per logo

```html
<!DOCTYPE html>
<html lang="en">
<head>
<meta charset="utf-8">
<title>The Pebble Hollow Garden – Australian Native Nursery</title>
<link rel="stylesheet" href="https://fonts.googleapis.com/css2?family=Questrial&display=swap">
<style>
:root{
  --ink:#2b2b2b;
  --muted:#555;
  --navy:#205c86;
  --navy-deep:#2a5d86;
  --teal:#17b6a0;
  --cream:#f5f2ec;
  --sand:#efe7dc;
  --white:#ffffff;
  --line:#d9d2c6;
}
*{box-sizing:border-box;margin:0;padding:0}
html,body{width:1200px;height:4121px;overflow:hidden}
body{font-family:"Questrial",sans-serif;color:var(--ink);background:var(--cream);position:relative}
a{color:inherit;text-decoration:none}
.abs{position:absolute}

/* header */
.site-header{position:absolute;left:0;top:0;width:1200px;height:67px;background:var(--white);border-top:3px solid var(--navy)}
.brand{position:absolute;left:100px;top:12px;display:flex;align-items:center;gap:10px;color:var(--navy);font-size:22px}
.brand-dot{width:36px;height:36px;border:1.5px solid var(--navy);border-radius:50%}
.main-nav{position:absolute;top:27px;left:440px;font-size:13px;color:var(--ink)}
.main-nav a{position:absolute;white-space:nowrap}
.main-nav .active{color:var(--navy)}
.nav-phone{position:absolute;left:944px;top:22px;font-size:13px;display:flex;align-items:center;gap:6px;border-left:1px solid #999;padding-left:14px}

/* hero */
.hero{position:absolute;left:0;top:67px;width:1200px;height:624px}
.hero-photo{position:absolute;inset:0;background:linear-gradient(100deg,#4a4536 0%,#6b5e48 35%,#7c6a52 55%,#8c7d66 75%,#5b5a44 100%)}
.hero-shade{position:absolute;inset:0;background:linear-gradient(90deg,rgba(0,0,0,.35),rgba(0,0,0,0) 60%)}
.hero-title{position:absolute;left:100px;top:222px;font-size:40px;font-weight:400;color:var(--white)}
.hero-text{position:absolute;left:100px;top:280px;font-size:15px;line-height:28px;color:var(--white)}
.btn-solid{position:absolute;display:flex;align-items:center;gap:6px;background:var(--navy);color:var(--white);font-size:12px;border-radius:20px;padding:0 16px}
.hero-btn{left:100px;top:357px;height:36px}
.hero-arrow{position:absolute;top:290px}
.hero-dots{position:absolute;left:557px;top:583px;display:flex;gap:12px}
.hero-dots span{width:11px;height:11px;border:1.5px solid var(--white);border-radius:50%}
.hero-dots .on{background:var(--white)}

/* shared headings */
.eyebrow{font-size:16px;color:var(--navy);letter-spacing:.5px;display:flex;align-items:center;gap:10px}
.eyebrow.center{position:absolute;left:0;width:1200px;justify-content:center;font-size:14px}
.eyebrow .rule{width:38px;height:1.5px;background:var(--navy)}
.section-title{position:absolute;left:0;width:1200px;text-align:center;font-size:37px;font-weight:400;color:var(--ink)}
.btn-outline{position:absolute;display:flex;align-items:center;gap:6px;border:1.5px solid var(--navy);color:var(--navy);font-size:12px;border-radius:20px;height:34px;padding:0 16px}

/* welcome */
.welcome{position:absolute;left:0;top:691px;width:1200px;height:595px;background:var(--cream)}
.welcome-photo{position:absolute;left:100px;top:63px;width:438px;height:462px;background:linear-gradient(160deg,#2aa6b8 0%,#1d8fa3 40%,#c9584a 70%,#efe8e0 100%)}
.badge{position:absolute;border-radius:50%;background:var(--white);border:1.5px solid #777;display:flex;align-items:center;justify-content:center;text-align:center;color:#444}
.welcome-badge{left:423px;top:378px;width:156px;height:156px;font-size:17px;line-height:22px}
.welcome-copy{position:absolute;left:655px;top:100px;width:445px}
.welcome-copy .eyebrow{font-size:22px}
.welcome-copy h2{font-weight:400;font-size:37px;margin-top:12px}
.welcome-copy p{font-size:14px;line-height:28px;color:var(--muted);text-align:justify;margin-top:12px}
.decor{position:absolute;background:rgba(180,180,180,.18);border-radius:50%}

/* nursery */
.nursery{position:absolute;left:0;top:1286px;width:1200px;height:1031px;background:var(--sand)}
.card{position:absolute;width:316px;height:380px;background:var(--white);padding:6px}
.card-photo{width:304px;height:230px}
.card h3{font-weight:400;font-size:19px;margin:14px 3px 6px}
.card p{font-size:12px;line-height:20px;color:var(--muted);margin:0 3px}
.card-link{display:flex;align-items:center;gap:4px;font-size:13px;color:var(--navy);text-decoration:underline;margin:4px 3px}

/* services */
.services{position:absolute;left:0;top:2317px;width:1200px;height:403px;background:var(--cream)}
.service{position:absolute;top:149px;width:240px;height:204px;background:var(--teal);color:var(--white);text-align:center;padding:18px 12px}
.service h3{font-weight:400;font-size:19px;margin-top:10px}
.service p{font-size:12px;line-height:20px;margin-top:8px;opacity:.92}

/* gift */
.gift{position:absolute;left:0;top:2720px;width:1200px;height:573px;background:var(--cream)}
.gift-copy{position:absolute;left:104px;top:88px;width:445px}
.gift-copy .eyebrow{font-size:23px}
.gift-copy h2{font-weight:400;font-size:37px;margin-top:10px}
.gift-copy p{font-size:14px;line-height:28px;color:var(--muted);text-align:justify;margin-top:10px}
.gift-copy p+p{margin-top:0}

/* contact */
.contact{position:absolute;left:0;top:3293px;width:1200px;height:499px;background:var(--sand)}
.contact-photo{position:absolute;left:0;top:0;width:430px;height:499px;background:linear-gradient(90deg,#b57a8a 0%,#c99aa2 45%,rgba(239,231,220,0) 100%)}
.field{position:absolute;background:var(--white);border:1px solid var(--line);font-size:13px;color:#444;padding:14px 16px}

/* footer */
.site-footer{position:absolute;left:0;top:3792px;width:1200px;height:329px;background:var(--navy-deep);color:var(--white)}
.footer-badge{left:100px;top:58px;width:200px;height:200px;background:transparent;border:2px solid var(--white);color:var(--white);font-size:22px;line-height:30px}
.fcol{position:absolute;top:55px}
.fcol h4{font-weight:400;font-size:17px;margin-bottom:14px}
.fcol li{list-style:none;font-size:13px;margin-bottom:17px}
.fcol p{font-size:13px;line-height:18px;margin-bottom:14px}
.sub-field{width:335px;height:36px;border:1px solid rgba(255,255,255,.7);font-size:11px;display:flex;align-items:center;justify-content:space-between;padding:0 12px;margin-bottom:14px}
.socials{display:flex;gap:10px;margin-top:4px}
.socials a{width:29px;height:29px;border:1.5px solid var(--white);border-radius:50%}
.footer-rule{position:absolute;left:100px;top:276px;width:1000px;height:1px;background:rgba(255,255,255,.5)}
.copyright{position:absolute;left:391px;top:295px;font-size:13px}
</style>
</head>
<body>

<header class="site-header">
  <a class="brand" href="#"><span class="brand-dot"></span>The Pebble Hollow Garden</a>
  <nav class="main-nav">
    <a class="active" style="left:0">HOME</a>
    <a style="left:80px">PLANTS</a>
    <a style="left:168px">GIFT SHOP</a>
    <a style="left:278px">OUR STORY</a>
    <a style="left:395px">CONTACT US</a>
  </nav>
  <div class="nav-phone">
    <svg width="11" height="11" viewBox="0 0 24 24"><path fill="#205c86" d="M6.6 10.8a15 15 0 0 0 6.6 6.6l2.2-2.2c.3-.3.7-.4 1-.2 1.1.4 2.3.6 3.6.6.6 0 1 .4 1 1V20c0 .6-.4 1-1 1A17 17 0 0 1 3 4c0-.6.4-1 1-1h3.5c.6 0 1 .4 1 1 0 1.3.2 2.5.6 3.6.1.3 0 .7-.2 1z"/></svg>
    +61 2 4210 7734
  </div>
</header>

<section class="hero">
  <div class="hero-photo" role="img" aria-label="Photo of the nursery shed with a flower mural and rows of potted native plants along a gravel path"></div>
  <div class="hero-shade"></div>
  <h1 class="hero-title">The Pebble Hollow Garden</h1>
  <p class="hero-text">Lorem ipsum dolor sit amet, consectetur adipiscing elit,<br>sed do eiusmod tempor incididunt ut labore</p>
  <a class="btn-solid hero-btn" href="#">GET STARTED
    <svg width="12" height="12" viewBox="0 0 24 24"><circle cx="12" cy="12" r="11" fill="#fff"/><path d="M10 7l5 5-5 5" stroke="#205c86" stroke-width="3" fill="none"/></svg></a>
  <svg class="hero-arrow" style="left:50px" width="24" height="46" viewBox="0 0 24 46"><path d="M22 2L2 23l20 21" stroke="#fff" stroke-width="2" fill="none"/></svg>
  <svg class="hero-arrow" style="left:1124px" width="24" height="46" viewBox="0 0 24 46"><path d="M2 2l20 21L2 44" stroke="#fff" stroke-width="2" fill="none"/></svg>
  <div class="hero-dots"><span></span><span class="on"></span><span></span><span></span></div>
</section>

<section class="welcome">
  <div class="decor" style="left:1080px;top:-10px;width:140px;height:140px" role="img" aria-label="Line drawing of a flannel flower"></div>
  <div class="decor" style="left:-40px;top:420px;width:130px;height:170px" role="img" aria-label="Line drawing of flannel flower leaves"></div>
  <div class="welcome-photo" role="img" aria-label="Photo of two nursery staff with a large native flower arrangement in a red pot"></div>
  <div class="badge welcome-badge">The Pebble<br>Hollow Garden</div>
  <div class="welcome-copy">
    <div class="eyebrow">WELCOME TO <span class="rule"></span></div>
    <h2>The Pebble Hollow Garden</h2>
    <p>At our nursery, we provide native plants that thrive in their local environment. Native plants are essential for preserving biodiversity, and they support pollinators and other wildlife while reducing human impact on the environment.</p>
    <p>At our nursery, we offer a wide selection of native plants that are suitable for a variety of different environments, and we provide planting and care instructions to ensure that your plants thrive once they're in the ground.</p>
  </div>
  <a class="btn-outline" href="#" style="left:655px;top:445px">LEARN MORE
    <svg width="12" height="12" viewBox="0 0 24 24"><circle cx="12" cy="12" r="11" fill="#205c86"/><path d="M10 7l5 5-5 5" stroke="#fff" stroke-width="3" fill="none"/></svg></a>
</section>

<section class="nursery">
  <div class="eyebrow center" style="top:76px"><span class="rule"></span>FLOWERS<span class="rule"></span></div>
  <h2 class="section-title" style="top:100px">Nursery Flowers</h2>

  <article class="card" style="left:100px;top:164px">
    <div class="card-photo" role="img" aria-label="Photo of white native flowers among dark green foliage" style="background:linear-gradient(135deg,#2f4a24,#6b8a4e 55%,#e6ebe0)"></div>
    <h3>The standard Lorem</h3>
    <p>Sed ut perspiciatis unde omnis istror sit voluptatem accusantium doloremque lau, totam rem aperiam, eaque ipsa quae ab illo inventore</p>
    <a class="card-link" href="#">LEARN MORE <svg width="12" height="12" viewBox="0 0 24 24"><circle cx="12" cy="12" r="11" fill="#205c86"/><path d="M10 7l5 5-5 5" stroke="#fff" stroke-width="3" fill="none"/></svg></a>
  </article>
  <article class="card" style="left:442px;top:164px">
    <div class="card-photo" role="img" aria-label="Photo of pink kangaroo paw flowers" style="background:linear-gradient(135deg,#3e5a2f,#d8708a 50%,#f0a4b4)"></div>
    <h3>The standard Lorem</h3>
    <p>Sed ut perspiciatis unde omnis istror sit voluptatem accusantium doloremque lau, totam rem aperiam, eaque ipsa quae ab illo inventore</p>
    <a class="card-link" href="#">LEARN MORE <svg width="12" height="12" viewBox="0 0 24 24"><circle cx="12" cy="12" r="11" fill="#205c86"/><path d="M10 7l5 5-5 5" stroke="#fff" stroke-width="3" fill="none"/></svg></a>
  </article>
  <article class="card" style="left:784px;top:164px">
    <div class="card-photo" role="img" aria-label="Photo of silver-leaved shrubs with small purple flowers outside a shed" style="background:linear-gradient(135deg,#6d6252,#b9c0b2 55%,#8f8aa6)"></div>
    <h3>The standard Lorem</h3>
    <p>Sed ut perspiciatis unde omnis istror sit voluptatem accusantium doloremque lau, totam rem aperiam, eaque ipsa quae ab illo inventore</p>
    <a class="card-link" href="#">LEARN MORE <svg width="12" height="12" viewBox="0 0 24 24"><circle cx="12" cy="12" r="11" fill="#205c86"/><path d="M10 7l5 5-5 5" stroke="#fff" stroke-width="3" fill="none"/></svg></a>
  </article>
  <article class="card" style="left:100px;top:572px">
    <div class="card-photo" role="img" aria-label="Photo of violet star-shaped flowers in pots" style="background:linear-gradient(135deg,#2d4a2a,#7f78c8 55%,#c7c3e8)"></div>
    <h3>The standard Lorem</h3>
    <p>Sed ut perspiciatis unde omnis istror sit voluptatem accusantium doloremque lau, totam rem aperiam, eaque ipsa quae ab illo inventore</p>
    <a class="card-link" href="#">LEARN MORE <svg width="12" height="12" viewBox="0 0 24 24"><circle cx="12" cy="12" r="11" fill="#205c86"/><path d="M10 7l5 5-5 5" stroke="#fff" stroke-width="3" fill="none"/></svg></a>
  </article>
  <article class="card" style="left:442px;top:572px">
    <div class="card-photo" role="img" aria-label="Photo of a single pink flower with dew drops" style="background:linear-gradient(135deg,#2e4a2c,#c77fc2 50%,#e7b4e0)"></div>
    <h3>The standard Lorem</h3>
    <p>Sed ut perspiciatis unde omnis istror sit voluptatem accusantium doloremque lau, totam rem aperiam, eaque ipsa quae ab illo inventore</p>
    <a class="card-link" href="#">LEARN MORE <svg width="12" height="12" viewBox="0 0 24 24"><circle cx="12" cy="12" r="11" fill="#205c86"/><path d="M10 7l5 5-5 5" stroke="#fff" stroke-width="3" fill="none"/></svg></a>
  </article>
  <article class="card" style="left:784px;top:572px">
    <div class="card-photo" role="img" aria-label="Photo of a colourful bunch of dried everlasting daisies" style="background:linear-gradient(135deg,#d9b24a,#e98a7a 50%,#f1e6d6)"></div>
    <h3>The standard Lorem</h3>
    <p>Sed ut perspiciatis unde omnis istror sit voluptatem accusantium doloremque lau, totam rem aperiam, eaque ipsa quae ab illo inventore</p>
    <a class="card-link" href="#">LEARN MORE <svg width="12" height="12" viewBox="0 0 24 24"><circle cx="12" cy="12" r="11" fill="#205c86"/><path d="M10 7l5 5-5 5" stroke="#fff" stroke-width="3" fill="none"/></svg></a>
  </article>
</section>

<section class="services">
  <div class="decor" style="left:1045px;top:0;width:160px;height:180px" role="img" aria-label="Line drawing of a flannel flower"></div>
  <div class="eyebrow center" style="top:60px"><span class="rule"></span>SERVICES<span class="rule"></span></div>
  <h2 class="section-title" style="top:84px">Native flowers</h2>

  <div class="service" style="left:100px">
    <svg width="62" height="70" viewBox="0 0 62 70" fill="none" stroke="#fff" stroke-width="2"><circle cx="31" cy="20" r="14"/><path d="M19 30l12 36 12-36M24 48h14"/></svg>
    <h3>Artisan Giftwear</h3>
    <p>Sed ut perspiciatis unde omnis istror sit volupm accusantium doloremque lau, totam rem aperiam</p>
  </div>
  <div class="service" style="left:353px">
    <svg width="62" height="70" viewBox="0 0 62 70" fill="none" stroke="#fff" stroke-width="2.5"><circle cx="24" cy="42" r="15"/><circle cx="38" cy="42" r="15"/><path d="M26 18l5-8 5 8z"/></svg>
    <h3>Weddings</h3>
    <p>Sed ut perspiciatis unde omnis istror sit volupm accusantium doloremque lau, totam rem aperiam</p>
  </div>
  <div class="service" style="left:606px">
    <svg width="70" height="70" viewBox="0 0 70 70" fill="none" stroke="#fff" stroke-width="2"><circle cx="22" cy="30" r="8"/><circle cx="48" cy="16" r="8"/><path d="M22 38l6 28M48 24L30 66"/></svg>
    <h3>special occasions</h3>
    <p>Sed ut perspiciatis unde omnis istror sit volupm accusantium doloremque lau, totam rem aperiam</p>
  </div>
  <div class="service" style="left:860px">
    <svg width="62" height="70" viewBox="0 0 62 70" fill="none" stroke="#fff" stroke-width="2"><path d="M14 66V30a17 17 0 0 1 34 0v36M8 66h46"/></svg>
    <h3>pictures</h3>
    <p>Sed ut perspiciatis unde omnis istror sit volupm accusantium doloremque lau, totam rem aperiam</p>
  </div>
</section>

<section class="gift">
  <div class="decor" style="left:-40px;top:410px;width:120px;height:150px" role="img" aria-label="Line drawing of a flannel flower"></div>
  <div class="gift-copy">
    <div class="eyebrow">GIFT SHOP <span class="rule"></span></div>
    <h2>Giftwear</h2>
    <p>We are proud to offer a wide range of unique and high-quality gifts that celebrate the natural beauty of Australia's native flora and fauna. From beautifully scented candles to stunning artworks, our gift selection is sure to please.</p>
    <p>Our giftware collection features a range of products that have been designed and crafted by local artisans and small businesses. We believe in supporting our community and showcasing the amazing talent</p>
  </div>
  <a class="btn-outline" href="#" style="left:104px;top:420px">LEARN MORE
    <svg width="12" height="12" viewBox="0 0 24 24"><circle cx="12" cy="12" r="11" fill="#205c86"/><path d="M10 7l5 5-5 5" stroke="#fff" stroke-width="3" fill="none"/></svg></a>
  <div class="abs" role="img" aria-label="Photo of wrapped native flower bouquets on a timber table" style="left:662px;top:38px;width:436px;height:346px;background:linear-gradient(135deg,#7a5a3a,#c3a88a 45%,#e9b7c4 75%,#b86a48)"></div>
  <div class="abs" role="img" aria-label="Photo of a small native arrangement in a driftwood holder" style="left:603px;top:232px;width:253px;height:256px;background:linear-gradient(160deg,#7e7b6e,#8f3a3c 45%,#b7a68c)"></div>
</section>

<section class="contact">
  <div class="contact-photo" role="img" aria-label="Photo of pink native blooms in a white painted jug"></div>
  <div class="eyebrow center" style="top:62px"><span class="rule"></span>CONTACT<span class="rule"></span></div>
  <h2 class="section-title" style="top:86px">Get In Touch</h2>
  <div class="field" style="left:282px;top:152px;width:312px;height:46px">First Name</div>
  <div class="field" style="left:605px;top:152px;width:313px;height:46px">Last Name</div>
  <div class="field" style="left:282px;top:209px;width:312px;height:46px">Phone No</div>
  <div class="field" style="left:605px;top:209px;width:313px;height:46px">Email Address</div>
  <div class="field" style="left:282px;top:267px;width:636px;height:116px">Message</div>
  <a class="btn-solid" href="#" style="left:531px;top:399px;height:34px;width:139px;justify-content:center">SUBMIT
    <svg width="12" height="12" viewBox="0 0 24 24"><circle cx="12" cy="12" r="11" fill="#fff"/><path d="M10 7l5 5-5 5" stroke="#205c86" stroke-width="3" fill="none"/></svg></a>
</section>

<footer class="site-footer">
  <div class="badge footer-badge">The Pebble<br>Hollow Garden</div>
  <div class="fcol" style="left:391px">
    <h4>Quick Links</h4>
    <ul><li>Home</li><li>Plants</li><li>Gift Shop</li><li>Our Story</li><li>Contact Us</li></ul>
  </div>
  <div class="fcol" style="left:536px;width:200px">
    <h4>Contact Info</h4>
    <p>18 Banksia Ridge Road, Kelmora, NSW, Australia, 2261</p>
    <p>+61 2 4210 7734</p>
    <p>hello@pebblehollowgarden.<br>com.au</p>
  </div>
  <div class="fcol" style="left:765px">
    <h4>Subscribe</h4>
    <div class="sub-field">Enter Your Email Address
      <svg width="16" height="16" viewBox="0 0 24 24"><path fill="#fff" d="M2 11l20-9-7 20-3-8z"/></svg></div>
    <p style="width:335px">Join our newsletter to stay up to date on promos &amp; launches.</p>
    <div class="socials">
      <a href="#" aria-label="Social link 1"></a>
      <a href="#" aria-label="Social link 2"></a>
      <a href="#" aria-label="Social link 3"></a>
      <a href="#" aria-label="Social link 4"></a>
    </div>
  </div>
  <div class="footer-rule"></div>
  <p class="copyright">©Copyright 2023 The Pebble Hollow Garden All Rights Reserved.</p>
</footer>

</body>
</html>
```